Sunscreen Package Design Modern SPF 50

Update current package design to a more modern design target women 16-40 Do not make it playful. SOLENVALE is home to movie stars and high income business people PalmSprings is one of the most desired vacation areas in the world. The sun shines 350 days a year. World class Tennis and Golf tournaments are held every year with the worlds top players attending these tournaments

Target Market(s)

Women

Industry/Entity Type

Skin Protection

Font styles to use
Sans Serif

Requirements
Must have
• The words SOLENVALE and KORIVELL

```html
<!DOCTYPE html>
<html lang="en">
<head>
<meta charset="utf-8">
<title>SOLENVALE KORIVELL Sunscreen SPF 50 – Range</title>
<link href="https://fonts.googleapis.com/css2?family=Cormorant+Garamond:wght@500&family=Montserrat:wght@400;500&display=swap" rel="stylesheet">
<style>
  :root {
    --bg: #e9e9e7;
    --ink: #2b2b2b;
    --cream: #ebdfcf;  --cream-cap: #b85f33;  --cream-spf: #c0653a;
    --sand: #d5cbc0;   --sand-cap: #6f675c;   --sand-spf: #7c7064;
    --mist: #a9bfc2;   --mist-cap: #2e4660;   --mist-spf: #34506b;
    --sage: #a6ae98;   --sage-cap: #4a5430;   --sage-spf: #4a5430;
    --slate: #47525a;  --slate-cap: #1f2833;  --slate-spf: #e08a3a;
  }
  * { margin: 0; padding: 0; box-sizing: border-box; }
  html, body { width: 1200px; height: 911px; overflow: hidden; background: var(--bg); }
  .range { position: relative; width: 1200px; height: 911px; }
  .tube { position: absolute; top: 163px; width: 213px; height: 588px; color: var(--ink); }
  .tube-body {
    position: absolute; left: 0; top: 0; width: 213px; height: 513px;
    background: var(--body);
    clip-path: polygon(0 0, 100% 0, 99% 30%, 85% 100%, 15% 100%, 1% 30%);
  }
  .tube-crimp {
    position: absolute; left: 0; top: 0; width: 100%; height: 20px;
    background: repeating-linear-gradient(90deg, rgba(0,0,0,.06) 0 1px, transparent 1px 3px);
  }
  .tube-cap {
    position: absolute; left: 46px; top: 510px; width: 121px; height: 78px;
    background: var(--cap); border-radius: 4px 4px 10px 10px;
  }
  .tube-cap::after {
    content: ""; position: absolute; left: 36px; top: 30px; width: 49px; height: 26px;
    border: 2px solid rgba(0,0,0,.18); border-radius: 2px;
  }
  .label { position: absolute; left: 0; width: 100%; text-align: center; white-space: nowrap; }
  .brand-name {
    font-family: "Montserrat", sans-serif; font-weight: 500; font-size: 21px;
    line-height: 26px; letter-spacing: 2.5px; top: 134px;
  }
  .sub-brand { font-family: "Montserrat", sans-serif; font-size: 9px; line-height: 12px; letter-spacing: 3px; top: 191px; }
  .divider { position: absolute; left: 106px; top: 219px; width: 1px; height: 73px; background: currentColor; }
  .product { font-family: "Montserrat", sans-serif; font-size: 9.5px; line-height: 12px; letter-spacing: 2.4px; top: 312px; }
  .spf-label { font-family: "Montserrat", sans-serif; font-size: 13px; line-height: 14px; top: 337px; color: var(--spf); }
  .spf-value {
    font-family: "Cormorant Garamond", serif; font-weight: 500; font-size: 42px; line-height: 36px;
    font-variant-numeric: lining-nums; top: 353px; color: var(--spf);
  }
  .claims { font-family: "Montserrat", sans-serif; font-size: 7.5px; line-height: 14px; top: 398px; letter-spacing: .2px; }
  .claims .spaced { letter-spacing: 1.2px; }
  .volume { font-family: "Montserrat", sans-serif; font-size: 8.5px; line-height: 12px; top: 472px; }
  .tube--cream { left: 43px;  --body: var(--cream); --cap: var(--cream-cap); --spf: var(--cream-spf); }
  .tube--sand  { left: 270px; --body: var(--sand);  --cap: var(--sand-cap);  --spf: var(--sand-spf); }
  .tube--mist  { left: 495px; --body: var(--mist);  --cap: var(--mist-cap);  --spf: var(--mist-spf); }
  .tube--sage  { left: 724px; --body: var(--sage);  --cap: var(--sage-cap);  --spf: var(--sage-spf); }
  .tube--slate { left: 950px; --body: var(--slate); --cap: var(--slate-cap); --spf: var(--slate-spf); color: #f2f0ec; }
</style>
</head>
<body>
<main class="range">
  <article class="tube tube--cream">
    <div class="tube-body"><div class="tube-crimp"></div></div>
    <div class="tube-cap"></div>
    <h2 class="label brand-name">SOLENVALE</h2>
    <p class="label sub-brand">KORIVELL</p>
    <span class="divider"></span>
    <p class="label product">SUNSCREEN</p>
    <p class="label spf-label">SPF</p>
    <p class="label spf-value">50</p>
    <p class="label claims">UVA + UVB PROTECTION<br><span class="spaced">BROAD SPECTRUM</span><br>WATER RESISTANT (80 MINUTES)</p>
    <p class="label volume">3 FL OZ / 88 mL</p>
  </article>
  <article class="tube tube--sand">
    <div class="tube-body"><div class="tube-crimp"></div></div>
    <div class="tube-cap"></div>
    <h2 class="label brand-name">SOLENVALE</h2>
    <p class="label sub-brand">KORIVELL</p>
    <span class="divider"></span>
    <p class="label product">SUNSCREEN</p>
    <p class="label spf-label">SPF</p>
    <p class="label spf-value">50</p>
    <p class="label claims">UVA + UVB PROTECTION<br><span class="spaced">BROAD SPECTRUM</span><br>WATER RESISTANT (80 MINUTES)</p>
    <p class="label volume">3 FL OZ / 88 mL</p>
  </article>
  <article class="tube tube--mist">
    <div class="tube-body"><div class="tube-crimp"></div></div>
    <div class="tube-cap"></div>
    <h2 class="label brand-name">SOLENVALE</h2>
    <p class="label sub-brand">KORIVELL</p>
    <span class="divider"></span>
    <p class="label product">SUNSCREEN</p>
    <p class="label spf-label">SPF</p>
    <p class="label spf-value">50</p>
    <p class="label claims">UVA + UVB PROTECTION<br><span class="spaced">BROAD SPECTRUM</span><br>WATER RESISTANT (80 MINUTES)</p>
    <p class="label volume">3 FL OZ / 88 mL</p>
  </article>
  <article class="tube tube--sage">
    <div class="tube-body"><div class="tube-crimp"></div></div>
    <div class="tube-cap"></div>
    <h2 class="label brand-name">SOLENVALE</h2>
    <p class="label sub-brand">KORIVELL</p>
    <span class="divider"></span>
    <p class="label product">SUNSCREEN</p>
    <p class="label spf-label">SPF</p>
    <p class="label spf-value">50</p>
    <p class="label claims">UVA + UVB PROTECTION<br><span class="spaced">BROAD SPECTRUM</span><br>WATER RESISTANT (80 MINUTES)</p>
    <p class="label volume">3 FL OZ / 88 mL</p>
  </article>
  <article class="tube tube--slate">
    <div class="tube-body"><div class="tube-crimp"></div></div>
    <div class="tube-cap"></div>
    <h2 class="label brand-name">SOLENVALE</h2>
    <p class="label sub-brand">KORIVELL</p>
    <span class="divider"></span>
    <p class="label product">SUNSCREEN</p>
    <p class="label spf-label">SPF</p>
    <p class="label spf-value">50</p>
    <p class="label claims">UVA + UVB PROTECTION<br><span class="spaced">BROAD SPECTRUM</span><br>WATER RESISTANT (80 MINUTES)</p>
    <p class="label volume">3 FL OZ / 88 mL</p>
  </article>
</main>
</body>
</html>
```